New career and executive coaching business needs a business card design including logo

Company name: 'Bramblefield Growth Partners.' The aim of my coaching engagements is to help people improve their communication in the workplace and achieve their career goals. The process involves working with individuals to help them uncover their strengths and talents, then leverage those to improve their working lives. The Tarwick Inventory is the starting point to the process. I am after an exciting and interesting business card design (including logo)which is professional yet will still get people's attention.

Industry/Entity Type

Business

Contact Information for Business Card

Name: Malcolm Dervaney
Position: Owner
Address: 58 Quorrin Ct, Elmbridge Vic 3190
Phone: 0418923047
Website: bramblefieldgrowth.com.au
Email: malcolm@bgp.com.au

Colors
33a6d7
00a990
0355a3
3176b5

Requirements
Must have
• logo

```html
<!DOCTYPE html>
<html lang="en">
<head>
<meta charset="utf-8">
<title>Bramblefield Growth Partners – Business Card</title>
<link rel="stylesheet" href="https://fonts.googleapis.com/css2?family=Tinos&family=Arimo&display=swap">
<style>
  :root {
    --page-bg: #e9e7e3;
    --card-white: #ffffff;
    --card-tint: #eef1f5;
    --brand-navy: #0355a3;
    --brand-blue: #3176b5;
    --brand-sky: #33a6d7;
    --text-light: #ffffff;
  }
  html, body {
    margin: 0;
    width: 1200px;
    height: 902px;
    overflow: hidden;
    background: var(--page-bg);
  }
  .card {
    position: absolute;
    left: 100px;
    top: 165px;
    width: 1000px;
    height: 572px;
    background: linear-gradient(180deg, var(--card-white) 0%, var(--card-tint) 60%);
    box-shadow: 0 10px 30px rgba(0,0,0,0.18);
    overflow: hidden;
  }
  .card-shapes {
    position: absolute;
    inset: 0;
  }
  .company-name {
    position: absolute;
    left: 0;
    right: 0;
    top: 108px;
    margin: 0;
    text-align: center;
    font-family: "Tinos", "Times New Roman", serif;
    font-weight: 400;
    font-size: 64px;
    line-height: 1.2;
    color: var(--brand-navy);
    letter-spacing: 0.5px;
  }
  .holder {
    position: absolute;
    left: 50px;
    bottom: 52px;
    color: var(--text-light);
  }
  .holder-name {
    margin: 0;
    font-family: "Tinos", "Times New Roman", serif;
    font-size: 46px;
    line-height: 1.05;
  }
  .holder-role {
    margin: 0;
    font-family: "Arimo", Arial, sans-serif;
    font-size: 30px;
    line-height: 1.1;
  }
  .contact {
    position: absolute;
    left: 500px;
    top: 365px;
    padding-left: 26px;
    border-left: 2px solid var(--text-light);
    list-style: none;
    margin: 0;
    font-family: "Arimo", Arial, sans-serif;
    font-size: 24px;
    color: var(--text-light);
  }
  .contact li {
    display: flex;
    align-items: center;
    gap: 14px;
    line-height: 36px;
  }
  .contact-icon {
    width: 18px;
    height: 18px;
    flex: none;
  }
</style>
</head>
<body>
  <div class="card">
    <svg class="card-shapes" viewBox="0 0 1000 572" width="1000" height="572" aria-hidden="true">
      <defs>
        <linearGradient id="bandFill" x1="0" y1="0" x2="0" y2="1">
          <stop offset="0" stop-color="#3176b5"/>
          <stop offset="1" stop-color="#0355a3"/>
        </linearGradient>
      </defs>
      <path d="M0 292 L40 292 L130 338 L985 234 L1000 212 L1000 572 L0 572 Z" fill="url(#bandFill)"/>
      <path d="M45 290 L130 313 L960 213 L992 184 L973 224 L130 327 Z" fill="#33a6d7"/>
    </svg>

    <h1 class="company-name">Bramblefield Growth Partners</h1>

    <div class="holder">
      <p class="holder-name">Malcolm Dervaney</p>
      <p class="holder-role">Owner</p>
    </div>

    <ul class="contact">
      <li>
        <svg class="contact-icon" viewBox="0 0 18 18"><rect width="18" height="18" rx="2" fill="#fff"/><path d="M5 4 L7 4 L8 7 L6.5 8 Q8 11 10 11.5 L11 10 L14 11 L14 13 Q9 14 5 9 Q4 6 5 4 Z" fill="#0355a3"/></svg>
        <span>0418923047</span>
      </li>
      <li>
        <svg class="contact-icon" viewBox="0 0 18 18"><rect width="18" height="18" rx="2" fill="#fff"/><rect x="3.5" y="5" width="11" height="8" fill="none" stroke="#0355a3" stroke-width="1.4"/><path d="M3.5 5 L9 9.5 L14.5 5" fill="none" stroke="#0355a3" stroke-width="1.4"/></svg>
        <span>malcolm@bgp.com.au</span>
      </li>
      <li>
        <svg class="contact-icon" viewBox="0 0 18 18"><rect width="18" height="18" rx="2" fill="#fff"/><circle cx="9" cy="9" r="5" fill="none" stroke="#0355a3" stroke-width="1.4"/><path d="M4 9 H14 M9 4 Q6 9 9 14 Q12 9 9 4" fill="none" stroke="#0355a3" stroke-width="1.2"/></svg>
        <span>bramblefieldgrowth.com.au</span>
      </li>
      <li>
        <svg class="contact-icon" viewBox="0 0 18 18"><rect width="18" height="18" rx="2" fill="#fff"/><path d="M9 15 Q4 9 4.5 7 A4.5 4.5 0 0 1 13.5 7 Q14 9 9 15 Z" fill="#0355a3"/><circle cx="9" cy="7" r="1.7" fill="#fff"/></svg>
        <span>58 Quorrin Ct, Elmbridge Vic 3190</span>
      </li>
    </ul>
  </div>
</body>
</html>
```